Website Redesign for Non-Profit Ministry & Church

NOTE: Please do not contact me privately — all private inquiries will be ignored.

Individuals seeking spiritual healing, community connection, ministry support and journal-based encounters.

Description of What’s Needed

We need a clean, fresh, inviting website that encourages engagement and connection. The site should feel warm and accessible, draw people in, and clearly present who we are, what we offer, and how visitors can participate. The layout should be straightforward, with well-structured pages (no overlapping objects, minimal layering complexity) and easy to navigate. Use only Google Fonts. All stock photos must be sourced from royalty-free sites and include proper attribution. We will not include a search feature.

Pages to Create
1. Home Page – impactful hero area, clear call-to-action, visual story of ministry, giving/gathering invitation.
2. About Us – vision, mission, leadership, testimonies, history.
3. Meetings & Events – upcoming gatherings, schedule, how to attend, sign-up or interest form.
4. Encounter: “Lanterns by the River” (book) – dedicated page for the book, overview, purchase link or details, journal prompts, imagery.
5. Healing Rooms / Ministry – explain ministry offerings, invite participation, testimonials or case-studies.
6. Live Stream & Links Page – page listing links for YouTube live stream, other platforms, archive links; simple layout.

Colour & Branding

Use colours that blend with our existing logo (attached). The palette should feel contemporary, welcoming, and aligned with ministry themes of restoration, healing and love. Ensure text, button and link colours maintain good contrast for accessibility.

Existing Content & Reference

Please gather available content from our current website in the attachment here for text, images and structure for reuse.

Imagery Guidelines

– Use original photos from our Friendbook page or Google Location listing for building or people images when available.
– If generic images are used, ensure they depict appropriate ministry-related buildings or people (community, warm gathering) — avoid generic unrelated stock imagery.
– All photos must be royalty-free or have proper licensing and attribution.
– No overlapping objects or visual clutter; clean layouts with defined sections.

Additional Notes

– Integration: We currently utilise MailChimp for email communication; the design should include a connection/invite to subscribe (via MailChimp) but no blog page is required at this time.
– Payment/Giving: We accept PayPal and already have a giving portal; include clear donation/give buttons or calls-to-action linking to existing giving systems.
– No search function to be included.
– Layouts should avoid complex layering or overlapping elements—designers should work with distinct content blocks, clear visual hierarchy, and straightforward mobile-friendly structure.

Target Market(s)

Industry/Entity Type

Church/Religious institution

Number of Pages Required

5+ page

Requirements
Should not have
• search bar

```html
<!DOCTYPE html>
<html lang="en">
<head>
<meta charset="utf-8">
<title>Mended Held Whole</title>
<link rel="stylesheet" href="https://fonts.googleapis.com/css2?family=Poppins:wght@400;500;600;700;800&display=swap">
<style>
:root{
  --green:#0f7a55;
  --green-dark:#0a5a3d;
  --green-deep:#06402b;
  --purple:#4b1a78;
  --ink:#2b2b2b;
  --muted:#6d6d6d;
  --white:#ffffff;
  --dark:#0b0b0b;
  --gold:#c9912e;
}
*{box-sizing:border-box;margin:0;padding:0}
html,body{width:1200px;height:4976px;overflow:hidden}
body{font-family:"Poppins",sans-serif;color:var(--ink);background:var(--white);position:relative}
.abs{position:absolute}
.btn{position:absolute;display:inline-block;background:var(--green);color:var(--white);font-weight:600;font-size:15px;padding:12px 26px;border-radius:22px;text-decoration:none;white-space:nowrap}
.section-title{font-weight:800;color:var(--purple);text-transform:uppercase;letter-spacing:.5px}
.photo{position:absolute;border-radius:14px}

/* hero */
.hero{position:absolute;left:0;top:0;width:1200px;height:700px;background:#2c2a28}
.hero-shade{position:absolute;inset:0;background:linear-gradient(90deg,rgba(0,0,0,.75),rgba(0,0,0,.2))}
.brand{position:absolute;left:110px;top:40px;display:flex;align-items:center;gap:12px;color:var(--white);font-weight:700;font-size:24px;line-height:1.05}
.brand-dot{width:34px;height:34px;border-radius:50%;background:var(--white)}
.nav{position:absolute;left:385px;top:112px;display:flex;gap:48px;color:var(--white);font-size:16px;font-weight:500}
.hero h1{position:absolute;left:110px;top:225px;color:var(--white);font-size:60px;font-weight:800;line-height:1.05}
.hero p{position:absolute;left:110px;top:385px;width:520px;color:var(--white);font-size:19px;line-height:1.55}

/* about */
.about h2{position:absolute;left:665px;top:745px;width:460px;font-size:46px;line-height:1.12}
.about p{position:absolute;left:665px;width:440px;font-size:17px;line-height:1.75;color:var(--muted)}

/* why */
.why h2{position:absolute;left:0;width:1200px;top:1430px;text-align:center;font-size:50px}
.why .lead{position:absolute;left:200px;width:800px;top:1505px;text-align:center;font-size:19px;line-height:1.5}
.card{position:absolute;top:1610px;width:200px;text-align:center}
.icon{width:116px;height:116px;border-radius:50%;border:3px solid var(--green);margin:0 auto 18px;display:flex;align-items:center;justify-content:center}
.card h3{color:var(--green);font-size:15px;font-weight:700;line-height:1.3;text-transform:uppercase}
.card p{font-size:12px;color:var(--muted);line-height:1.5;margin-top:8px}

/* blogs */
.blogs h2{position:absolute;left:0;width:1200px;top:2160px;text-align:center;color:var(--white);font-size:50px;font-weight:800}
.blogs .lead{position:absolute;left:220px;width:760px;top:2235px;text-align:center;color:var(--white);font-size:19px;line-height:1.5}
.blog{position:absolute;top:2330px;width:246px;height:330px;border-radius:16px;overflow:hidden;background:var(--green-deep)}
.blog .pic{height:240px}
.blog h4{color:var(--white);font-size:16px;font-weight:600;text-align:center;padding:18px 20px;line-height:1.35}

/* follow */
.follow h2{position:absolute;left:0;width:1200px;top:2955px;text-align:center;font-size:50px}

/* invite */
.invite h2{position:absolute;left:110px;top:3570px;width:470px;font-size:48px;line-height:1.12}
.invite p{position:absolute;left:110px;width:450px;font-size:17px;line-height:1.7;color:var(--muted)}

/* newsletter */
.news h2{position:absolute;left:0;width:1200px;top:4215px;text-align:center;font-size:48px}
.news p{position:absolute;left:300px;width:600px;top:4290px;text-align:center;font-size:15px;line-height:1.6;color:var(--muted)}
.field{position:absolute;left:270px;top:4385px;width:440px;height:54px;border-radius:27px;background:var(--white);box-shadow:0 2px 12px rgba(0,0,0,.12);padding:16px 26px;font-size:14px;color:var(--muted)}

/* footer */
.footer{position:absolute;left:0;top:4560px;width:1200px;height:416px;background:var(--dark);color:var(--white)}
.footer h5{font-size:22px;font-weight:700;margin-bottom:20px}
.footer li{list-style:none;font-size:15px;margin-bottom:14px;display:flex;align-items:center;gap:12px}
.bullet{width:10px;height:10px;border-radius:50%;background:var(--white);flex:none}
.copy{position:absolute;left:0;width:1200px;top:380px;text-align:center;font-size:14px;color:#cfcfcf}
</style>
</head>
<body>

<section class="hero">
  <div role="img" aria-label="Photo of a preacher speaking to a seated congregation" class="abs" style="inset:0;background:linear-gradient(120deg,#3a332c,#6b5a48 50%,#2a2622)"></div>
  <div class="hero-shade"></div>
  <div class="brand"><span class="brand-dot"></span><span>Mended<br>Held<br>Whole</span></div>
  <nav class="nav"><span>Home</span><span>About Us</span><span>Meetings &amp; Events</span><span>Encounter</span><span>Healing Rooms / Ministry</span></nav>
  <a class="btn" style="left:945px;top:45px">Give Now</a>
  <h1>MENDED, HELD,<br>WHOLE</h1>
  <p>Honoring God’s presence by loving the broken, saving the lost, and healing the hurting through the demonstration of His love and power.</p>
  <a class="btn" style="left:110px;top:500px">Give Now</a>
</section>
<svg class="abs" style="left:0;top:520px" width="1200" height="240" viewBox="0 0 1200 240">
  <path d="M0 120 C300 230 600 20 900 60 C1020 75 1120 100 1200 70 L1200 240 L0 240Z" fill="#0f7a55"/>
  <path d="M0 150 C300 250 620 50 900 95 C1030 115 1120 130 1200 110 L1200 240 L0 240Z" fill="#ffffff"/>
</svg>

<section class="about">
  <div role="img" aria-label="Golden ribbon butterfly ornament" class="abs" style="left:120px;top:770px;width:320px;height:600px;border-radius:40%;background:radial-gradient(circle,#f3cf7a,#c9912e 55%,#fff 72%)"></div>
  <h2 class="section-title">A Home for Restoration and Renewal</h2>
  <p style="top:1025px">Honoring God’s presence by loving the broken, saving the lost, and healing the hurting through the demonstration of His love and power.</p>
  <p style="top:1160px">Mended, Held, Whole is here to activate, proclaim and teach the love of the Father through Jesus with the guidance of the Holy Spirit.</p>
  <a class="btn" style="left:665px;top:1285px">Read More</a>
</section>

<section class="why">
  <h2 class="section-title">Why Choose Us?</h2>
  <p class="lead">Through teaching, activation, and discipleship, we help people encounter God and walk confidently in their identity and purpose.</p>
  <div class="card" style="left:175px">
    <div class="icon"><svg width="56" height="56" viewBox="0 0 56 56"><rect x="22" y="6" width="12" height="44" rx="4" fill="#0f7a55" transform="rotate(45 28 28)"/><rect x="22" y="6" width="12" height="44" rx="4" fill="#0f7a55" transform="rotate(-45 28 28)"/></svg></div>
    <h3>Hearts Deserve Healing</h3>
    <p>At Mended, Held, Whole, we don’t just talk about God’s love – we demonstrate it, live it, and invite others to experience it.</p>
  </div>
  <div class="card" style="left:395px;top:1585px">
    <div class="icon"><svg width="56" height="56" viewBox="0 0 56 56"><circle cx="28" cy="18" r="9" fill="#0f7a55"/><path d="M10 48c2-12 10-17 18-17s16 5 18 17Z" fill="#0f7a55"/></svg></div>
    <h3>We Lead With the Father’s Heart</h3>
    <p>We carry a heart for the broken and a passion to see lives transformed through Jesus.</p>
  </div>
  <div class="card" style="left:615px">
    <div class="icon"><svg width="56" height="56" viewBox="0 0 56 56"><path d="M28 6C14 18 12 34 28 50C44 34 42 18 28 6Z" fill="#0f7a55"/><path d="M28 14V46" stroke="#fff" stroke-width="3"/></svg></div>
    <h3>Healing Through the Power</h3>
    <p>We create space for the Holy Spirit to move in freedom, bringing restoration to hearts, minds, and bodies.</p>
  </div>
  <div class="card" style="left:835px;top:1585px">
    <div class="icon"><svg width="56" height="56" viewBox="0 0 56 56"><path d="M28 48L9 29a11 11 0 0 1 19-14a11 11 0 0 1 19 14Z" fill="#0f7a55"/><path d="M28 22v14M21 29h14" stroke="#fff" stroke-width="4"/></svg></div>
    <h3>Authentic Love in Action</h3>
    <p>We minister with compassion, humility, and genuine care – reflecting Jesus in every encounter.</p>
  </div>
</section>

<svg class="abs" style="left:0;top:1900px" width="1200" height="960" viewBox="0 0 1200 960">
  <defs><linearGradient id="band" x1="0" y1="0" x2="1" y2="1"><stop offset="0" stop-color="#0a5a3d"/><stop offset=".5" stop-color="#0f7a55"/><stop offset="1" stop-color="#06402b"/></linearGradient></defs>
  <path d="M0 80 C300 0 600 160 900 110 C1040 85 1130 40 1200 20 L1200 880 C900 960 600 800 300 860 C180 885 80 900 0 880Z" fill="url(#band)"/>
</svg>
<section class="blogs">
  <h2>OUR LATEST BLOGS</h2>
  <p class="lead">Whether you’re just beginning your faith journey or growing in ministry, our teachings help you lead with clarity and impact.</p>
  <article class="blog" style="left:108px"><div class="pic" role="img" aria-label="Congregation gathered in worship" style="background:linear-gradient(160deg,#6e5b49,#3b3129)"></div><h4>Nothing is incurable for God</h4></article>
  <article class="blog" style="left:360px"><div class="pic" role="img" aria-label="Prayer ministry at the altar" style="background:linear-gradient(160deg,#5a4a3e,#2d2520)"></div><h4>Healing amidst the car accident</h4></article>
  <article class="blog" style="left:612px"><div class="pic" role="img" aria-label="Worshippers with raised hands" style="background:linear-gradient(160deg,#4f5e73,#2a3140)"></div><h4>Why is healing important?</h4></article>
  <article class="blog" style="left:864px"><div class="pic" role="img" aria-label="Hands reaching toward sunlight" style="background:linear-gradient(160deg,#f2d8a4,#9e7c4f)"></div><h4>Now is the time to move!</h4></article>
  <a class="btn" style="left:520px;top:2690px;background:var(--white);color:var(--green)">View More Blogs</a>
</section>

<section class="follow">
  <h2 class="section-title">Follow Us on Friendbook</h2>
  <div class="photo" role="img" aria-label="Church building exterior with blue sky" style="left:108px;top:3060px;width:232px;height:330px;background:linear-gradient(180deg,#5d8fd1,#8a5b45 65%,#6c8f4a)"></div>
  <div class="photo" role="img" aria-label="Church members together" style="left:354px;top:3060px;width:232px;height:330px;background:linear-gradient(180deg,#cdbfae,#6b4a5c)"></div>
  <div class="photo" role="img" aria-label="Worship gathering in the sanctuary" style="left:600px;top:3060px;width:232px;height:330px;background:linear-gradient(180deg,#9aa9b3,#3f3a36)"></div>
  <div class="photo" role="img" aria-label="Outdoor gathering on the lawn" style="left:846px;top:3060px;width:246px;height:330px;background:linear-gradient(180deg,#b7c7d9,#6b8a4c)"></div>
  <a class="btn" style="left:538px;top:3440px">Follow Us</a>
</section>

<section class="invite">
  <h2 class="section-title">You’re Invited to Gather With Us.</h2>
  <p style="top:3720px">Whether you’re exploring faith, seeking community, or longing for a place to belong, you are welcome here. We meet each week to worship, pray, and encounter God’s love together.</p>
  <p style="top:3865px">We’d love to meet you. Our gatherings are filled with worship, encouragement, and genuine community.</p>
  <a class="btn" style="left:110px;top:3960px">Get In Touch</a>
  <div role="img" aria-label="Green leaf ornament framing the gathering photo" class="abs" style="left:580px;top:3540px;width:440px;height:480px;border-radius:50%;background:radial-gradient(circle,rgba(15,122,85,.35),rgba(15,122,85,.12) 60%,rgba(255,255,255,0) 72%)"></div>
  <div role="img" aria-label="Congregation seated in the church hall" class="abs" style="left:640px;top:3620px;width:320px;height:320px;border-radius:50%;background:linear-gradient(160deg,#a9a49a,#5c4f45)"></div>
</section>

<section class="news">
  <svg class="abs" style="left:560px;top:4115px" width="80" height="80" viewBox="0 0 80 80">
    <path d="M8 34 L40 10 L72 34 V72 H8Z" fill="#0f7a55"/>
    <rect x="18" y="18" width="44" height="30" fill="#ffffff"/>
    <path d="M26 28h28M26 36h20" stroke="#0f7a55" stroke-width="3"/>
    <path d="M8 34 L40 56 L72 34" fill="none" stroke="#ffffff" stroke-width="3"/>
  </svg>
  <h2 class="section-title">Join Our Newsletter</h2>
  <p>Receive weekly encouragement, gathering updates, healing testimonies and news from our community, delivered straight to your inbox so you never miss a moment together.</p>
  <div class="field">Enter Email Address</div>
  <a class="btn" style="left:720px;top:4385px;padding:16px 32px">Subscribe Now</a>
</section>

<svg class="abs" style="left:0;top:4440px" width="1200" height="140" viewBox="0 0 1200 140">
  <path d="M0 90 C300 140 700 20 1200 40 L1200 140 L0 140Z" fill="#0f7a55"/>
  <path d="M0 115 C320 150 720 60 1200 80 L1200 140 L0 140Z" fill="#0b0b0b"/>
</svg>
<footer class="footer">
  <div class="brand" style="left:110px;top:80px;font-size:30px"><span class="brand-dot" style="width:42px;height:42px"></span><span>Mended<br>Held<br>Whole</span></div>
  <div class="abs" style="left:450px;top:60px"><h5>QUICK LINKS</h5><ul>
    <li><span class="bullet"></span>Home</li><li><span class="bullet"></span>About Us</li><li><span class="bullet"></span>Our Products</li><li><span class="bullet"></span>Services</li><li><span class="bullet"></span>Contact Us</li></ul></div>
  <div class="abs" style="left:640px;top:60px;width:290px"><h5>CONTACT INFO</h5><ul>
    <li><svg width="14" height="18" viewBox="0 0 14 18"><path d="M7 0a7 7 0 0 1 7 7c0 5-7 11-7 11S0 12 0 7a7 7 0 0 1 7-7Z" fill="#fff"/><circle cx="7" cy="7" r="2.5" fill="#0b0b0b"/></svg>1420 Cedar Hollow Lane, Fairfield,</li>
    <li style="padding-left:26px">United States, 00000</li>
    <li><svg width="16" height="12" viewBox="0 0 16 12"><rect width="16" height="12" rx="2" fill="#fff"/><path d="M1 1l7 6 7-6" stroke="#0b0b0b" fill="none"/></svg>hello@mendedheldwhole.org</li>
    <li><svg width="14" height="14" viewBox="0 0 14 14"><path d="M3 0l3 3-2 2c1 2 3 4 5 5l2-2 3 3-2 3C6 14 0 8 0 3Z" fill="#fff"/></svg>+1 555-010-2468</li></ul></div>
  <div class="abs" style="left:960px;top:60px"><h5>FOLLOW US</h5><ul>
    <li><span class="bullet"></span>Friendbook</li><li><span class="bullet"></span>Chirper</li><li><span class="bullet"></span>Snapshare</li></ul></div>
  <div class="abs" style="left:110px;top:345px;width:980px;height:1px;background:#444"></div>
  <a class="btn" style="left:945px;top:355px;padding:8px 20px;font-size:14px">Let’s Talk</a>
  <p class="copy">(C) Copyright 2025 | All Rights Reserved</p>
</footer>

</body>
</html>
```